Hartwell Estates Business Cards

I would like a business card that includes myself and my partner.
Includes: Logo, office #, email, website, our names, our numbers and possibly the address. I would also like the logo to be embossed and the card to be horizontal.
There is a photo of our yard signs to give you an idea of the colors of our business.

Target Market(s)

Everyone in real estate market.
We are in a rural area. Our clientele are from all socioeconomic backgrounds.

Industry/Entity Type

Real Estate Agent

Contact Information for Business Card

Company Name: Hartwell Estates
Our Names, Titles & Cell #'s : Dana Pembrook-Broker (555).317.6624, Marla Pembrook-Realtor (555).609.1385
Office #: (555).240.3918
Website: hartwellestates-demo.com
Joint Email: pembrook@hartwellestates-demo.com
Office Address: 418B W. Calloway Ave.
Linden Falls, OR. 70913

Font styles to use
Serif

Requirements
Must have
• HORIZONTAL, Logo, Myself and my partners names, Our cell #'s, our office #, our website, our email address
Nice to have
• Embossed logo, office address, our titles.

```html
<!DOCTYPE html>
<html lang="en">
<head>
<meta charset="utf-8">
<title>Hartwell Estates Business Card</title>
<link rel="stylesheet" href="https://fonts.googleapis.com/css2?family=PT+Sans:wght@400;700&display=swap">
<style>
  :root {
    --backdrop: #d8d3cd;
    --card: #efece8;
    --plum: #2f2145;
    --ink: #55505a;
    --band-text: #cfc6dc;
  }
  * { box-sizing: border-box; margin: 0; padding: 0; }
  html, body {
    width: 1200px;
    height: 969px;
    overflow: hidden;
    background: var(--backdrop);
    font-family: "PT Sans", sans-serif;
  }
  .business-card {
    position: absolute;
    left: 100px;
    top: 200px;
    width: 1000px;
    height: 570px;
    background: var(--card);
    border-radius: 6px;
    box-shadow: 0 18px 40px rgba(40, 30, 50, 0.18);
    overflow: hidden;
  }
  .brand {
    position: absolute;
    left: 52px;
    top: 82px;
    display: flex;
    align-items: center;
    gap: 22px;
  }
  .brand-mark {
    width: 84px;
    height: 84px;
    border-radius: 50%;
    background: var(--plum);
  }
  .brand-name {
    font-weight: 700;
    font-size: 56px;
    color: var(--plum);
    letter-spacing: 1px;
    line-height: 1;
  }
  .office-details {
    position: absolute;
    left: 52px;
    top: 290px;
    color: var(--ink);
    font-size: 25px;
    line-height: 35px;
    font-style: normal;
  }
  .office-details .phone { margin-top: 16px; }
  .office-details .label { font-weight: 700; color: var(--plum); }
  .agents {
    position: absolute;
    right: 48px;
    top: 286px;
    text-align: right;
    color: var(--ink);
  }
  .agent-name {
    font-weight: 700;
    font-size: 33px;
    color: var(--plum);
    line-height: 40px;
  }
  .agent-title {
    font-weight: 400;
    font-size: 25px;
    color: var(--ink);
    margin-left: 8px;
  }
  .agent-phone {
    font-size: 25px;
    line-height: 36px;
  }
  .website-band {
    position: absolute;
    left: 0;
    right: 0;
    top: 499px;
    height: 50px;
    background: var(--plum);
    color: var(--band-text);
    font-size: 26px;
    letter-spacing: 4px;
    text-align: center;
    line-height: 50px;
  }
</style>
</head>
<body>
  <section class="business-card">
    <div class="brand">
      <div class="brand-mark"></div>
      <div class="brand-name">Hartwell Estates</div>
    </div>

    <address class="office-details">
      <div>418B W. Calloway Ave.</div>
      <div>Linden Falls, OR. 70913</div>
      <div class="phone"><span class="label">Phone:</span> (555).240.3918</div>
      <div>pembrook@hartwellestates-demo.com</div>
    </address>

    <div class="agents">
      <div class="agent-name">Dana Pembrook,<span class="agent-title">Broker</span></div>
      <div class="agent-phone">(555).317.6624</div>
      <div class="agent-name">Marla Pembrook,<span class="agent-title">Realtor</span></div>
      <div class="agent-phone">(555).609.1385</div>
    </div>

    <div class="website-band">www.hartwellestates-demo.com</div>
  </section>
</body>
</html>
```